Business Card Design Project

We have recently completed CraftHive projects for a new logo and wesbite.
We now require new business cards.
We hand out very little printed material to clients as all information is online. When we do hand out something, like a business card, we want it to have real impact and make a statement about the quality and professionalism of our company.
We have an idea of what we want our card to look like but we want a designer to make sure they have impact and look great.
Our requirements are…
Size: 85mm X 55mm - Landscape
Front of card: Logo plus the following contact information.
Dennis Marlow
Operations Manager
Phone +44(0) 1632 xxx xxx
Mobile +44(0) 7700 xxx xxx
Email denmo@korvantix.example
Address 17 Pellick Row, Aberdeen AB12 9QZ
Website www.korvantix.example
How you layout the front of the card is up to you, we would like to see some different ideas. Attached are two versions of our logo that may be used.
Back of card: We would like this to be simple but again have impact. Our current thought is to have the logo or just the large W design from the logo in white against a dark background, perhaps made up from the dark green in the logo.
The logos are attached so you can see the colours in them but the dark ones are..
Dark Blue = C:88, M:55, Y:44, K:28
Dark Green = C:87, M:53, Y:50, K:50
We sometimes also use a bright orange as an accent or highlight colour…
Orange: = C:0, M:39, Y:94, K:0

```html
<!DOCTYPE html>
<html lang="en">
<head>
<meta charset="utf-8">
<title>Korvantix Business Cards</title>
<link rel="stylesheet" href="https://fonts.googleapis.com/css2?family=Open+Sans:wght@400;600;700&display=swap">
<style>
  :root {
    --canvas: #e9e6e1;
    --card-white: #ffffff;
    --teal-dark: #22424a;
    --green-soft: #7b915d;
    --ink: #1f2a2e;
    --ink-soft: #3b4548;
    --white: #ffffff;
  }
  * { margin: 0; padding: 0; box-sizing: border-box; }
  html, body {
    width: 1200px; height: 800px; overflow: hidden;
    background: var(--canvas);
    font-family: "Open Sans", Arial, sans-serif;
  }
  .sheet { position: relative; width: 1200px; height: 800px; }

  .card {
    position: absolute; width: 502px; height: 324px;
    border-radius: 16px; overflow: hidden;
    box-shadow: 0 3px 10px rgba(0,0,0,0.18);
  }
  .card--front { left: 82px; top: 62px; background: var(--card-white); }
  .card--back-dark { left: 610px; top: 66px; background: var(--teal-dark); }
  .card--back-gradient { left: 84px; top: 408px; background: linear-gradient(90deg, var(--teal-dark) 0%, var(--green-soft) 100%); }
  .card--back-light { left: 610px; top: 408px; background: var(--card-white); }

  /* brand lockup */
  .brand { display: flex; align-items: center; gap: 12px; }
  .brand__dot { border-radius: 50%; flex: none; }
  .brand__name { font-weight: 700; letter-spacing: 1px; line-height: 1; }

  .card--front .brand { position: absolute; left: 26px; top: 148px; }
  .card--front .brand__dot { width: 34px; height: 34px; background: var(--teal-dark); }
  .card--front .brand__name { font-size: 32px; color: var(--teal-dark); }

  .contact { position: absolute; left: 293px; top: 66px; color: var(--ink); }
  .contact__name { font-size: 17px; font-weight: 400; text-transform: uppercase; letter-spacing: 0.2px; line-height: 22px; }
  .contact__role { font-size: 12.5px; color: var(--ink-soft); line-height: 18px; }
  .contact__list { list-style: none; margin-top: 16px; }
  .contact__item { display: flex; align-items: center; gap: 5px; font-size: 12.5px; line-height: 19px; color: var(--ink-soft); }
  .contact__icon { width: 11px; height: 11px; flex: none; }
  .contact__address { font-style: normal; margin-top: 16px; font-size: 12.5px; line-height: 19px; color: var(--ink-soft); }

  .bands { position: absolute; left: 0; right: 0; top: 276px; height: 10px; display: flex; gap: 7px; }
  .bands__dark { width: 289px; background: var(--teal-dark); }
  .bands__green { flex: 1; background: var(--green-soft); }

  /* back faces */
  .back-brand { position: absolute; left: 0; right: 0; top: 108px; justify-content: center; }
  .back-brand .brand__dot { width: 52px; height: 52px; }
  .back-brand .brand__name { font-size: 50px; }
  .back-brand--white .brand__dot { background: var(--white); }
  .back-brand--white .brand__name { color: var(--white); }
  .back-brand--teal .brand__dot { background: var(--teal-dark); }
  .back-brand--teal .brand__name { color: var(--teal-dark); }

  .web { position: absolute; left: 0; right: 0; top: 266px; text-align: center; font-size: 15px; letter-spacing: 2.6px; }
  .web--white { color: var(--white); }
  .web--teal { color: var(--teal-dark); }
</style>
</head>
<body>
<main class="sheet">

  <section class="card card--front" aria-label="Card front">
    <div class="brand">
      <span class="brand__dot"></span>
      <span class="brand__name">KORVANTIX</span>
    </div>

    <div class="contact">
      <h1 class="contact__name">Dennis Marlow</h1>
      <p class="contact__role">Operations Manager</p>
      <ul class="contact__list">
        <li class="contact__item">
          <svg class="contact__icon" viewBox="0 0 12 12" aria-hidden="true"><circle cx="6" cy="6" r="5.3" fill="none" stroke="#3b4548" stroke-width="1"/><path d="M4 3.2 L5.2 4.6 L4.6 5.3 Q5.5 7 6.9 7.5 L7.5 6.9 L8.8 8 L8 9 Q5.5 8.8 3.6 5.6 Q3.3 4 4 3.2Z" fill="#3b4548"/></svg>
          +44(0) 1632 xxx xxx
        </li>
        <li class="contact__item">
          <svg class="contact__icon" viewBox="0 0 12 12" aria-hidden="true"><rect x="3" y="0.8" width="6" height="10.4" rx="1" fill="#3b4548"/><rect x="4" y="2" width="4" height="6" fill="#fff"/><circle cx="6" cy="9.5" r="0.7" fill="#fff"/></svg>
          +44(0) 7700 xxx xxx
        </li>
        <li class="contact__item">
          <svg class="contact__icon" viewBox="0 0 12 12" aria-hidden="true"><rect x="0.8" y="3" width="10.4" height="7" fill="#3b4548"/><path d="M0.8 3 L6 7 L11.2 3" fill="none" stroke="#fff" stroke-width="0.9"/></svg>
          denmo@korvantix.example
        </li>
        <li class="contact__item">
          <svg class="contact__icon" viewBox="0 0 12 12" aria-hidden="true"><circle cx="6" cy="6" r="5" fill="none" stroke="#3b4548" stroke-width="1"/><ellipse cx="6" cy="6" rx="2.2" ry="5" fill="none" stroke="#3b4548" stroke-width="0.8"/><path d="M1 6 H11 M2 3.5 H10 M2 8.5 H10" stroke="#3b4548" stroke-width="0.7"/></svg>
          www.korvantix.example
        </li>
      </ul>
      <address class="contact__address">17 Pellick Row,<br>Aberdeen AB12 9QZ</address>
    </div>

    <div class="bands"><span class="bands__dark"></span><span class="bands__green"></span></div>
  </section>

  <section class="card card--back-dark" aria-label="Card back, dark">
    <div class="brand back-brand back-brand--white">
      <span class="brand__dot"></span>
      <span class="brand__name">KORVANTIX</span>
    </div>
    <p class="web web--white">www.korvantix.example</p>
  </section>

  <section class="card card--back-gradient" aria-label="Card back, gradient">
    <div class="brand back-brand back-brand--white">
      <span class="brand__dot"></span>
      <span class="brand__name">KORVANTIX</span>
    </div>
    <p class="web web--white">www.korvantix.example</p>
  </section>

  <section class="card card--back-light" aria-label="Card back, light">
    <div class="brand back-brand back-brand--teal">
      <span class="brand__dot"></span>
      <span class="brand__name">KORVANTIX</span>
    </div>
    <p class="web web--teal">www.korvantix.example</p>
  </section>

</main>
</body>
</html>
```